RTavenor Business Cards & Letterhead

I have a logo but need a design for some new business cards. We are a Design-Build Firm that specializes in the design and construction of commercial projects.
the cards need to be professional. no cartoon stuff.
i would like to have the cards in AI format so I can update the card as needed. Logo is provided.
Our Address is: 4187 Marlowe Ct. Apex, North Carolina 27614

```html
<!DOCTYPE html>
<html lang="en">
<head>
<meta charset="utf-8">
<title>RTavenor Business Card</title>
<link href="https://fonts.googleapis.com/css2?family=Roboto:wght@400;700&display=swap" rel="stylesheet">
<style>
  :root {
    --bg: #3b3b3b;
    --card-front: #f6f6f6;
    --card-back: #383838;
    --brand-blue: #0a67a0;
    --ink: #4a4a4a;
    --ink-soft: #6a6a6a;
    --rule: #555555;
    --logo-grey: #555555;
    --white: #f4f4f4;
  }
  * { margin: 0; padding: 0; box-sizing: border-box; }
  html, body { width: 1200px; height: 1200px; overflow: hidden; }
  body {
    background: var(--bg);
    font-family: "Roboto", Arial, sans-serif;
    position: relative;
  }
  .card {
    position: absolute;
    left: 262px;
    width: 686px;
    height: 392px;
    border-radius: 22px;
  }
  .card--front { top: 165px; background: var(--card-front); }
  .card--back { top: 653px; background: var(--card-back); }

  .wordmark {
    position: absolute;
    display: flex;
    align-items: center;
    font-weight: 700;
    letter-spacing: 0.5px;
    line-height: 1;
  }
  .wordmark__square { background: var(--brand-blue); flex: none; }
  .card--front .wordmark {
    right: 50px; top: 62px;
    font-size: 36px; color: var(--logo-grey); gap: 8px;
  }
  .card--front .wordmark__square { width: 28px; height: 28px; }
  .card--back .wordmark {
    left: 0; right: 0; top: 160px; justify-content: center;
    font-size: 68px; color: var(--white); gap: 14px;
  }
  .card--back .wordmark__square { width: 52px; height: 52px; }

  .person { position: absolute; left: 47px; top: 221px; }
  .person__name { font-size: 26px; font-weight: 700; color: var(--brand-blue); line-height: 1.1; }
  .person__title { font-size: 15px; color: var(--ink-soft); margin-top: 2px; }
  .divider {
    position: absolute; left: 47px; top: 276px; width: 592px;
    height: 1px; background: var(--rule);
  }
  .contacts {
    position: absolute; left: 47px; top: 286px;
    list-style: none; font-size: 16px; color: var(--ink); line-height: 20.5px;
  }
  .contacts li { display: flex; align-items: center; gap: 9px; }
  .contacts svg { width: 14px; height: 14px; fill: var(--brand-blue); flex: none; }
  .address {
    position: absolute; right: 47px; top: 289px;
    text-align: right; font-style: normal;
    font-size: 16px; color: var(--ink); line-height: 20.5px;
  }
  .address__web { color: var(--brand-blue); margin-right: -4px; }
</style>
</head>
<body>
  <section class="card card--front">
    <div class="wordmark"><span class="wordmark__square"></span>RTAVENOR</div>
    <div class="person">
      <h1 class="person__name">Daniel Whitford</h1>
      <p class="person__title">Managing Director</p>
    </div>
    <div class="divider"></div>
    <ul class="contacts">
      <li>
        <svg viewBox="0 0 16 16" aria-hidden="true"><path d="M3.2 1.2l2.4 0.2 1.2 3.2-1.7 1.3c0.9 1.9 2.2 3.2 4.1 4.1l1.3-1.7 3.2 1.2 0.2 2.4c-0.2 1.3-1.3 2.2-2.6 2.1C6 13.6 2.4 10 1.1 3.8 1 2.5 1.9 1.4 3.2 1.2z"/></svg>
        936-555-0142
      </li>
      <li>
        <svg viewBox="0 0 16 16" aria-hidden="true"><path d="M4 0.5h8a1 1 0 0 1 1 1v13a1 1 0 0 1-1 1H4a1 1 0 0 1-1-1v-13a1 1 0 0 1 1-1zm0.8 2v9.5h6.4V2.5zM8 12.6a0.9 0.9 0 1 0 0 1.8 0.9 0.9 0 0 0 0-1.8z"/></svg>
        936-555-0187
      </li>
      <li>
        <svg viewBox="0 0 16 16" aria-hidden="true"><path d="M1 3.5h14v9H1zm1.4 1.2v0.3L8 9l5.6-4v-0.3zM2.4 6.6v4.7h11.2V6.6L8 10.6z"/></svg>
        info@rtavenor.com
      </li>
    </ul>
    <address class="address">
      4187 Marlowe Ct. Apex<br>
      North Carolina 27614<br>
      <span class="address__web">www.rtavenor.com</span>
    </address>
  </section>

  <section class="card card--back">
    <div class="wordmark"><span class="wordmark__square"></span>RTAVENOR</div>
  </section>
</body>
</html>
```